Locksmith Business Cards

My father-in-law is in need of new business cards for his locksmith business and I need to impress him. Kindly help me out!

You can see the previous business card attached. It is a family run business in North Wales.

No individual names on the cards.

Key Things to Feature:
- The words "Prompt", "Local", "Reliable" (as you can see under the logo on the website)
- 24h Emergency Service
- Covering All of North Wales, the Wirral and Chester
- The color blue
- A key or a lock would be interesting (similar to the ones that come up when you google locksmith business card)

Optional (only if design includes bullet points, like the example below):
https://imgvaultcdn.net/samples/208314/55172/55172_3904821_208314_image.jpg
- Residential / Commercial / Automotive
- Alarms & Cameras
- Key Cutting & Safes

https://www.brynhafod-locksmiths.co.uk/

Industry/Entity Type

Locksmith

Contact Information for Business Card

01632 960 418
07700 900 362
brynhafodlocksmiths@mailvane.com
Brynhafod Locksmiths, The Willow Barn, 7 Tannery Rd., Llandudno LL99 4QX
www.brynhafod-locksmiths.co.uk

Requirements
Must have
• - The words "Prompt", "Local", "Reliable" (as you can see under the logo on the website)
• - 24h Emergency Service
• - Covering All of North Wales, the Wirral and Chester
Nice to have
• - A key or a lock would be interesting (similar to the ones that come up when you google locksmith business card)

```html
<!DOCTYPE html>
<html lang="en">
<head>
<meta charset="utf-8">
<title>Brynhafod Locksmiths – Business Card</title>
<link rel="stylesheet" href="https://fonts.googleapis.com/css2?family=Open+Sans:ital,wght@0,400;0,600;0,700;1,700&display=swap">
<style>
  :root {
    --navy: #1f2a6b;
    --navy-deep: #1a2360;
    --white: #ffffff;
    --ink: #1e1e24;
    --backdrop: #e9e9ec;
    --rule: #2b3785;
  }
  * { box-sizing: border-box; margin: 0; padding: 0; }
  html, body { width: 1200px; height: 1200px; overflow: hidden; }
  body {
    background: var(--backdrop);
    font-family: "Open Sans", Arial, sans-serif;
    position: relative;
  }
  .card {
    position: absolute;
    left: 220px;
    width: 760px;
    height: 434px;
    box-shadow: 0 6px 18px rgba(0,0,0,0.18);
  }
  /* Back of card */
  .card-back {
    top: 150px;
    background: var(--navy);
    border-radius: 80px 0 80px 0;
    color: var(--white);
  }
  .services {
    list-style: none;
    position: absolute;
    left: 70px;
    top: 92px;
    font-weight: 700;
    font-style: italic;
    font-size: 31px;
    line-height: 1.45;
  }
  .services li::before {
    content: "";
    display: inline-block;
    width: 12px; height: 12px;
    border-radius: 50%;
    background: var(--white);
    margin-right: 10px;
    vertical-align: 8px;
  }
  /* Front of card */
  .card-front {
    top: 616px;
    background: var(--white);
    border-radius: 0 80px 0 80px;
    color: var(--ink);
  }
  .brand {
    position: absolute;
    right: 48px;
    top: 60px;
    display: flex;
    align-items: center;
    gap: 14px;
  }
  .brand-square {
    width: 58px; height: 58px;
    background: var(--navy);
  }
  .brand-name {
    color: var(--navy);
    font-weight: 700;
    font-size: 34px;
    line-height: 1.05;
    text-transform: uppercase;
    letter-spacing: 0.5px;
  }
  .tagline {
    position: absolute;
    right: 60px;
    top: 144px;
    color: var(--navy);
    font-weight: 700;
    font-style: italic;
    font-size: 19px;
  }
  .address {
    position: absolute;
    right: 48px;
    top: 200px;
    text-align: right;
    font-size: 20px;
    line-height: 1.35;
    font-style: normal;
  }
  .contacts {
    list-style: none;
    position: absolute;
    left: 42px;
    top: 176px;
    font-size: 20px;
    line-height: 1.3;
  }
  .contacts li { display: flex; align-items: center; gap: 8px; }
  .contacts svg { width: 16px; height: 16px; fill: var(--navy-deep); flex: none; }
  .service-band {
    position: absolute;
    left: 30px; right: 60px;
    top: 334px;
    display: flex;
    align-items: center;
    gap: 10px;
  }
  .service-band::before, .service-band::after {
    content: ""; flex: 1; height: 1.5px; background: var(--rule);
  }
  .service-band span {
    color: var(--navy);
    font-weight: 600;
    font-size: 20px;
    text-transform: uppercase;
  }
  .coverage {
    position: absolute;
    left: 0; right: 30px;
    top: 366px;
    text-align: center;
    font-size: 20px;
  }
</style>
</head>
<body>
  <section class="card card-back">
    <ul class="services">
      <li>Residential / Commercial / Automotive</li>
      <li>Alarms &amp; Cameras</li>
      <li>Key Cutting &amp; Safes</li>
    </ul>
  </section>

  <section class="card card-front">
    <div class="brand">
      <span class="brand-square"></span>
      <span class="brand-name">Brynhafod<br>Locksmiths</span>
    </div>
    <p class="tagline">Prompt. Local. Reliable</p>

    <address class="address">
      Brynhafod Locksmiths<br>
      The Willow Barn<br>
      7 Tannery Rd., Llandudno<br>
      LL99 4QX
    </address>

    <ul class="contacts">
      <li><svg viewBox="0 0 16 16"><path d="M1 5c0-2 2-3 7-3s7 1 7 3v1h-4V5H5v1H1zM3 7h10l1 7H2z"/></svg>01632 960 418</li>
      <li><svg viewBox="0 0 16 16"><path d="M4 0h8v16H4zM5.5 1.5v11h5v-11z"/></svg>07700 900 362</li>
      <li><svg viewBox="0 0 16 16"><path d="M0 3h16v10H0zM1.5 4.5 8 9l6.5-4.5z"/></svg>brynhafodlocksmiths@mailvane.com</li>
      <li><svg viewBox="0 0 16 16"><circle cx="8" cy="8" r="7"/></svg>www.brynhafod-locksmiths.co.uk</li>
    </ul>

    <div class="service-band"><span>24H Emergency Service</span></div>
    <p class="coverage">Covering All of North Wales, the Wirral and Chester</p>
  </section>
</body>
</html>
```